Commercial Refrigeration Service Company requires stylish and fresh looking flyer.

We need a flyer to hand out to new customers. It should have a photo and our branding, list all the services that are offered and our contact details.
We would like two flyers to be supplied, both identical though one offering a discount until July ( Half Price Service Fee ). The flyer should be clear, interesting and in similar colours to the branding package supplied.
Please look at our website for information about the services on offer:
www.brisko-coolworks.com.au

Target Market(s)

Cafes, bars, restaurants, pubs ect.

Font styles to use
Other font styles liked:
• Font package provided

Colors
85cae6
ffffff
333333

Requirements
Must have
• - The photo provided.
• - The company logo.
• - Similar feel to the website & business card.
• - Smooth layout and clear to understand.
Should not have
• - No clunky badges or prints.

```html
<!DOCTYPE html>
<html lang="en">
<head>
<meta charset="utf-8">
<title>Brisko Commercial Refrigeration – Flyer</title>
<link href="https://fonts.googleapis.com/css2?family=Josefin+Sans:wght@400;600&family=Quicksand:wght@400;500&display=swap" rel="stylesheet">
<style>
  :root {
    --blue: #85cae6;
    --blue-strong: #5ec4ee;
    --charcoal: #333333;
    --white: #ffffff;
    --page: #d9d9d9;
  }
  * { box-sizing: border-box; margin: 0; padding: 0; }
  html, body { width: 1200px; height: 1029px; overflow: hidden; }
  body { background: var(--page); font-family: "Quicksand", sans-serif; }

  .flyer {
    position: absolute; left: 80px; width: 1040px; height: 490px;
    background: var(--charcoal); overflow: hidden;
  }
  .flyer--front { top: 16px; }
  .flyer--back { top: 523px; }

  /* Front */
  .hero-photo {
    position: absolute; left: 0; top: 0; width: 1040px; height: 400px;
    background: linear-gradient(180deg, #9fc6e6 0%, #c7dcec 30%, #7f8ba4 58%, #5b6276 80%, #6b6458 100%);
  }
  .offer-badge {
    position: absolute; left: 22px; top: 20px; width: 160px; height: 160px;
    border-radius: 50%; background: var(--charcoal);
    box-shadow: 0 0 0 6px rgba(255,255,255,.35), 0 0 0 7px rgba(255,255,255,.7);
    display: flex; flex-direction: column; justify-content: center; align-items: center;
    transform: rotate(-20deg);
    font-family: "Josefin Sans", sans-serif; font-weight: 400; font-size: 19px;
    line-height: 1.05; text-align: center; letter-spacing: .5px;
  }
  .offer-badge .offer-main { color: var(--white); }
  .offer-badge .offer-sub { color: var(--blue-strong); }
  .services-strip {
    position: absolute; left: 0; bottom: 0; width: 100%; height: 90px;
    display: flex; align-items: center; justify-content: center;
    font-family: "Josefin Sans", sans-serif; font-weight: 400; font-size: 27px;
    letter-spacing: 3.5px; color: var(--blue-strong);
  }

  /* Back */
  .about {
    position: absolute; left: 48px; top: 34px; width: 440px;
    color: var(--white); font-size: 15.5px; line-height: 1.45;
  }
  .about p + p { margin-top: 10px; }
  .contact-email {
    position: absolute; left: 48px; top: 352px;
    font-size: 19px; color: var(--blue-strong); text-transform: uppercase;
  }
  .divider {
    position: absolute; left: 520px; top: 30px; width: 1px; height: 340px;
    background: rgba(255,255,255,.45);
  }
  .brand {
    position: absolute; left: 560px; top: 70px; width: 440px;
    text-align: center;
  }
  .brand-name {
    font-family: "Quicksand", sans-serif; font-weight: 500; font-size: 48px;
    letter-spacing: 2px; line-height: 1; color: var(--white);
  }
  .brand-tagline {
    margin-top: 44px; font-family: "Josefin Sans", sans-serif; font-weight: 400;
    font-size: 29px; letter-spacing: 3px; line-height: 1.3; color: var(--blue-strong);
  }
  .partner-badge {
    position: absolute; right: 48px; top: 300px; width: 96px; height: 40px;
    border: 1.5px solid rgba(255,255,255,.7); border-radius: 4px;
  }
  .contact-web {
    position: absolute; right: 40px; top: 356px;
    font-size: 19px; color: var(--blue-strong); text-transform: uppercase;
  }
  .call-strip {
    position: absolute; left: 0; bottom: 0; width: 100%; height: 72px;
    background: var(--blue-strong);
    display: flex; align-items: center; justify-content: center;
    font-family: "Josefin Sans", sans-serif; font-weight: 600; font-size: 25px;
    letter-spacing: 4px; color: var(--charcoal);
  }
</style>
</head>
<body>

<section class="flyer flyer--front">
  <div class="hero-photo" role="img" aria-label="Photo of the technician standing beside the branded service ute parked at the beach"></div>
  <div class="offer-badge">
    <span class="offer-main">HALF PRICE</span>
    <span class="offer-main">SERVICE FEE</span>
    <span class="offer-sub">DISCOUNTED</span>
    <span class="offer-sub">UNTIL JULY</span>
  </div>
  <div class="services-strip">COMMERCIAL REFRIGERATION, ICEMAKERS &amp; BEER SYSTEMS</div>
</section>

<section class="flyer flyer--back">
  <div class="about">
    <p>Brisko Refrigeration is a company based in Eastern Sydney, providing commercial refrigeration and electrical services.</p>
    <p>Sam and his team believe in developing tight relationships with their clients and keeping things simple by offering a personalised service – speak to the same people and see the same faces.</p>
    <p>Brisko is completely paperless and uses cloud based trade service software to build a complete profile of your venue and equipment, allowing Sam to offer tailored advice for your business.</p>
  </div>
  <div class="contact-email">info@brisko-coolworks.com.au</div>

  <div class="divider"></div>

  <div class="brand">
    <div class="brand-name">Brisko</div>
    <div class="brand-tagline">24HR SERVICE, SALES &amp;<br>INSTALLATIONS</div>
  </div>
  <div class="partner-badge"></div>
  <div class="contact-web">www.brisko-coolworks.com.au</div>

  <div class="call-strip">CALL SAM HARLOW 0412 550 918</div>
</section>

</body>
</html>
```